Local fast-growing company in the service sector

We are looking for a modern business card design, which should also appear on our letterheads

Target Market(s)

Private and industrial sectors

Contact Information for Business Card

Vorname Name
Kellberger Str. 18
74219 Kellbach
Tel.: 07146-839214-0
Name@agentur-kvtl.de

Colors
9d9d9d
919191
aaaaaa

Requirements
Must have
• The logo (file) in silver

```html
<!DOCTYPE html>
<html lang="de">
<head>
<meta charset="utf-8">
<title>KVTL Visitenkarte</title>
<link rel="stylesheet" href="https://fonts.googleapis.com/css2?family=Open+Sans:wght@400;600;700&display=swap">
<style>
  :root {
    --stage: #000000;
    --card: #313236;
    --card-edge: #36373b;
    --silver: #aaaaaa;
    --silver-mid: #9d9d9d;
    --text-light: #f2f2f2;
    --text-body: #dcdcdc;
    --divider: #45464b;
  }
  * { box-sizing: border-box; margin: 0; padding: 0; }
  html, body { width: 1200px; height: 900px; overflow: hidden; background: var(--stage); }
  body { position: relative; font-family: "Open Sans", Arial, sans-serif; }

  .card {
    position: absolute;
    top: 271px;
    width: 457px;
    height: 281px;
    border-radius: 14px;
    background: radial-gradient(ellipse at 50% 40%, var(--card-edge), var(--card) 70%);
  }
  .card--front { left: 137px; }
  .card--back  { left: 626px; }

  .brand-mark {
    position: absolute;
    display: flex;
    align-items: center;
    gap: 12px;
    color: var(--silver);
    font-weight: 700;
    letter-spacing: 1px;
  }
  .brand-mark__square { background: var(--silver-mid); }

  .card--front .brand-mark { left: 58px; top: 112px; font-size: 40px; }
  .card--front .brand-mark__square { width: 26px; height: 26px; }

  .card--front .divider {
    position: absolute;
    left: 232px; top: 78px;
    width: 1px; height: 122px;
    background: var(--divider);
  }

  .contact {
    position: absolute;
    left: 259px; top: 80px;
    color: var(--text-body);
    font-size: 12.5px;
    line-height: 17px;
  }
  .contact__name {
    color: var(--text-light);
    font-size: 15px;
    font-weight: 600;
    margin-bottom: 12px;
  }
  .contact__address { margin-bottom: 9px; }
  .contact__line { display: flex; align-items: center; gap: 6px; }
  .contact__line svg { width: 11px; height: 11px; fill: var(--text-body); flex: none; }

  .card--back .brand-mark { left: 0; right: 0; top: 100px; justify-content: center; font-size: 56px; }
  .card--back .brand-mark__square { width: 40px; height: 40px; }
</style>
</head>
<body>
  <section class="card card--front" aria-label="Vorderseite">
    <div class="brand-mark"><span class="brand-mark__square"></span>KVTL</div>
    <div class="divider"></div>
    <div class="contact">
      <p class="contact__name">VORNAME NAME</p>
      <p class="contact__address">Kellberger Str. 18<br>74219 Kellbach</p>
      <p class="contact__line">
        <svg viewBox="0 0 12 12" aria-hidden="true"><path d="M2.5 0.8l2 2-1.1 1.4c.7 1.5 1.9 2.7 3.4 3.4l1.4-1.1 2 2-1.3 1.9C5 10.2 1.8 7 1 2.1z"/></svg>
        07146-839214-0
      </p>
      <p class="contact__line">
        <svg viewBox="0 0 12 12" aria-hidden="true"><path d="M0.5 2.5h11v7h-11z M0.5 2.5l5.5 4 5.5-4" fill="none" stroke="#dcdcdc" stroke-width="1"/><path d="M0.5 2.5h11L6 6.3z"/></svg>
        Name@agentur-kvtl.de
      </p>
      <p class="contact__line">
        <svg viewBox="0 0 12 12" aria-hidden="true"><circle cx="6" cy="6" r="5.3"/><path d="M3 4.5c1-.6 2 .4 1.5 1.3-.6.8.6 1.8 1.2 2.8M7.5 2.2c.6.8 0 1.5.9 2 .8.4 1.8 0 2.3.8" fill="none" stroke="#323337" stroke-width="1"/></svg>
        www.agentur-kvtl.de
      </p>
    </div>
  </section>

  <section class="card card--back" aria-label="Rückseite">
    <div class="brand-mark"><span class="brand-mark__square"></span>KVTL</div>
  </section>
</body>
</html>
```